Contractor Plan "B"/Getting Screwed?/Something Useful

We are sending out a series of postcards to a group of local contractors.

The first in the series is: Plan B: Pink Bubble Wrap. Plan A is to buy insurance from my agency. This will be printed, front and back on card stock. We will then glue a piece of bubble wrap to the card and place it in an envelope for delivery.

The second card will be along the same lines but will ask if the client is getting screwed by his current Insurance Company. We will glue a screw in the middle of the card and place the card in an envelope for delivery. On the bottom of we might tell them to call us to get unscrewed.

The third card will follow those lines but say something like: We sent you bubble wrap for your Plan B and you didn't call. Then we sent you something funny but you didn't call. We decided to send you something useful so you might call now! With this card, we are going to send a carpenter pencil.

I am attaching a rough outline of my sketch design for the first card so you will have basic information we will need such as phone number and coverages we offer. If you feel like there is too much info for the size of the card, we can leave some off. I just want the phone to ring! Also, feel free to adjust the wording to make it work better...creative design is not my strong suit!!

I would like for all three cards to be designed. Each can have the same backside. Also, please keep in mind, this is not a postcard so you don't have to leave the blanks on the back for addressing. Each will be mailed in an envelope.

I have also uploaded my logo file as we have recently redone the logo.
Updates

Here is more guidance on the project: The cards are going to be 10 cm wide and 23 cm tall. I have added more wording in the brief. Also, I attached a word doc with a good idea of what to use for wording. Basically I want the following idea: Card 1: At top of card - Plan B: Pink Bubble Wrap Below the bubble wrap - Plan A: Call us so you don't have to use Pink Bubble Wrap Card 2: At top of card - Getting Screwed? Is your current agent taking you for granted? Below the area where we are going to glue a screw - Get unscrewed, Call us! Card 3: At top of card - We have the sharpest pencil in town! We will leave space for a carpenter pencil to be attached tot he card. On the other side of the open space - Call us today for the best rates on your insurance!

Please review the attached word doc for an idea of what to put on the back of the card. To be clear, we need three designs for the front of the card and can probably use just one design for the back of all three. If you think we need to have a different design for the back of each, I would like to see your ideas. Thank you for your hard work on these!

Reason: Hi, I am extending the time as I am expecting a few more submissions. Thank you!

Target Market(s)

We are targeting both contractors and truckers with this campaign.

Industry/Entity Type

Insurance

Requirements
Must have
• Clever wording. It needs to be a call to action and doesn't need to have too many specifics.

We also have to have space in the middle to glue the bubble wrap on the first card, the screw in the second and attach the pencil in the third.

```html
<!DOCTYPE html>
<html lang="en">
<head>
<meta charset="utf-8">
<title>Plan B – Pink Bubble Wrap Card</title>
<link rel="stylesheet" href="https://fonts.googleapis.com/css2?family=Oswald:wght@300;700&family=Archivo+Black&family=Montserrat:wght@400&display=swap">
<style>
  :root {
    --ink: #0d0d0d;
    --paper: #ffffff;
    --magenta: #e3168c;
    --wrap-light: #f2aef1;
    --wrap-mid: #e08ae0;
    --wrap-deep: #cc66cf;
    --brand-red: #c8202f;
  }
  html, body {
    margin: 0;
    padding: 0;
    width: 1200px;
    height: 2759px;
    overflow: hidden;
    background: var(--paper);
  }
  .card {
    display: block;
    width: 1200px;
    height: 2759px;
    background: var(--paper);
  }
  .condensed-bold { font-family: "Oswald", "Arial Narrow", sans-serif; font-weight: 700; fill: var(--ink); }
  .condensed-light { font-family: "Oswald", "Arial Narrow", sans-serif; font-weight: 300; fill: var(--ink); }
  .heavy { font-family: "Archivo Black", "Arial Black", sans-serif; fill: var(--ink); }
  .headline { font-size: 470px; }
  .lead { font-size: 100px; }
  .product { font-size: 112px; fill: var(--magenta); }
  .cta { font-size: 155px; }
  .phone { font-size: 136px; }
  .question { font-size: 172px; }
  .accent { fill: var(--magenta); }
  .quip { font-size: 58px; }
  .brand-name { font-size: 46px; }
  .brand-mark { fill: var(--brand-red); }
  .address { font-family: "Montserrat", Arial, sans-serif; font-weight: 400; font-size: 36px; fill: var(--ink); }
</style>
</head>
<body>
  <svg class="card" viewBox="0 0 1200 2759" xmlns="http://www.w3.org/2000/svg">
    <defs>
      <radialGradient id="wrap-shine-a" cx="0.3" cy="0.35" r="0.55">
        <stop offset="0" stop-color="var(--wrap-light)"/>
        <stop offset="1" stop-color="var(--wrap-mid)" stop-opacity="0"/>
      </radialGradient>
      <linearGradient id="wrap-base" x1="0" y1="0" x2="1" y2="1">
        <stop offset="0" stop-color="var(--wrap-mid)"/>
        <stop offset="1" stop-color="var(--wrap-deep)"/>
      </linearGradient>
    </defs>

    <text class="condensed-bold headline" x="97" y="542" textLength="1001" lengthAdjust="spacingAndGlyphs">Plan B</text>
    <text class="condensed-light lead" x="80" y="709" textLength="1004" lengthAdjust="spacingAndGlyphs">Protect your business with</text>
    <text class="heavy product" x="80" y="840" textLength="1004" lengthAdjust="spacingAndGlyphs">Pink Bubble Wrap</text>

    <g role="img" aria-label="Close-up photo of pink bubble wrap">
      <rect x="47" y="912" width="1115" height="745" fill="url(#wrap-base)"/>
      <rect x="47" y="912" width="1115" height="745" fill="url(#wrap-shine-a)"/>
    </g>

    <text class="condensed-bold cta" x="80" y="1849" textLength="1032" lengthAdjust="spacingAndGlyphs">Call us to avoid Plan B</text>
    <text class="heavy phone" x="80" y="2018" textLength="1032" lengthAdjust="spacingAndGlyphs">555-014-2236</text>
    <text class="heavy question" x="80" y="2182" textLength="1026" lengthAdjust="spacingAndGlyphs">Why <tspan class="accent">pink</tspan>?</text>
    <text class="condensed-light quip" x="80" y="2307" textLength="1004" lengthAdjust="spacingAndGlyphs">You might not get sued if they think you are a wuss.</text>

    <g class="brand">
      <rect class="brand-mark" x="385" y="2537" width="44" height="44"/>
      <text class="heavy brand-name" x="447" y="2576" textLength="370" lengthAdjust="spacingAndGlyphs">Lone Oak Insurance</text>
    </g>
    <text class="address" x="600" y="2719" text-anchor="middle">4100 Larkspur Ln, Oakfield, Texas 77000</text>
  </svg>
</body>
</html>
```